Larkspur Talent IT Recruiting firm needs a business card design for Recruiters, Sourcers, and Account

We need business cards that allow us to change all contact info, names, titles (Recruiter, Sourcer, Account Manager, Director, CEO, etc) per person since we have three offices, in three cities, Phoenix, Austin, and Las Vegas. We do recruiting and contractors for IT positions (Developers, Architects, Software Engineers, Security Engineers, Help Desk, DBAs, PMs, Scrum Masters, etc.) Our client companies are very diverse from Meridian 100 to silicone Valley type start-ups.

So, while we what hip, techie, and quirky, it still needs to be professional. Primary color we use is blue, with silver as a secondary color.

Target Market(s)

IT, Technology

Industry/Entity Type

Business

Contact Information for Business Card

Company name: Larkspur Talent, Inc.
Website: www.larkspurtalent.example
Logos for Careerloop, Blipster, and Myriada

Name, Title, Office Number, Cell Number, email

Font styles to use
Serif
Sans Serif

Colors
0455a3
d5d5d5

Requirements
Nice to have
• The grey I selected below is not necessary - but, would like silver included. I included a card design (File 3: LTI early trial example.jpg) that I had started on. It's very rough, and not quite what we're looking for, but what we did like is the logo, big, maybe a bit faded, off center, goes out of frame, etc. Still looking for other ideas - you are the pros! But, just an idea of a design element we liked.

```html
<!DOCTYPE html>
<html lang="en">
<head>
<meta charset="utf-8">
<title>Larkspur Talent – Business Card</title>
<link rel="stylesheet" href="https://fonts.googleapis.com/css2?family=Marcellus&family=PT+Sans:wght@400;700&display=swap">
<style>
  :root {
    --stage: #1f1f1f;
    --card-white: #ffffff;
    --brand-blue: #0455a3;
    --brand-blue-light: #0a93d8;
    --ink: #231f20;
    --swoosh-grey: #555555;
    --back-grey: #575757;
    --silver: #d5d5d5;
    --text-grey: #4a4a4a;
  }
  * { margin: 0; padding: 0; box-sizing: border-box; }
  html, body {
    width: 1200px; height: 907px; overflow: hidden;
    background: var(--stage);
  }
  .stage { position: relative; width: 1200px; height: 907px; }

  .card {
    position: absolute; left: 300px; width: 600px; height: 343px;
    overflow: hidden;
    box-shadow: 0 4px 14px rgba(0,0,0,.55);
  }
  .card--front { top: 98px; background: var(--card-white); }
  .card--back { top: 475px; background: var(--back-grey); }

  .card__swoosh { position: absolute; inset: 0; width: 600px; height: 343px; }

  .wordmark {
    font-family: "Marcellus", serif;
    display: flex; align-items: center; gap: 10px;
    letter-spacing: 2px; text-transform: uppercase; white-space: nowrap;
  }
  .wordmark__dot { width: 24px; height: 24px; border-radius: 50%; flex: none; }
  .tagline {
    font-family: "Marcellus", serif; text-transform: uppercase;
    letter-spacing: 1.6px; white-space: nowrap;
  }

  .card--front .brand { position: absolute; left: 50px; top: 62px; }
  .card--front .wordmark { font-size: 29px; color: var(--ink); }
  .card--front .wordmark__dot { background: var(--brand-blue); }
  .card--front .tagline { font-size: 14px; color: var(--ink); margin-top: 14px; }

  .person { position: absolute; left: 50px; top: 228px; font-family: "PT Sans", sans-serif; }
  .person__name { font-size: 25px; color: var(--brand-blue); line-height: 1.1; }
  .person__title { font-size: 18px; color: var(--text-grey); margin-top: 4px; }

  .contact {
    position: absolute; right: 50px; top: 212px;
    list-style: none; font-family: "PT Sans", sans-serif;
    font-size: 15px; color: #ffffff; text-align: right;
  }
  .contact__row { display: flex; align-items: center; justify-content: flex-end; gap: 9px; height: 22.5px; }
  .contact__icon { width: 14px; height: 14px; flex: none; }

  .card--back .brand {
    position: absolute; left: 0; right: 0; top: 126px;
    display: flex; flex-direction: column; align-items: center;
  }
  .card--back .wordmark { font-size: 32px; color: #ffffff; }
  .card--back .wordmark__dot { background: #ffffff; }
  .card--back .tagline { font-size: 15px; color: #ffffff; margin-top: 18px; }

  .social {
    position: absolute; left: 0; right: 0; top: 291px;
    display: flex; justify-content: center; gap: 18px;
    list-style: none; font-family: "PT Sans", sans-serif; font-size: 13px; color: var(--silver);
  }
  .social__item { display: flex; align-items: center; gap: 6px; }
  .social__square { width: 14px; height: 14px; background: var(--brand-blue); border-radius: 2px; }
</style>
</head>
<body>
<main class="stage">

  <section class="card card--front" aria-label="Business card front">
    <svg class="card__swoosh" viewBox="0 0 600 343" aria-hidden="true">
      <defs>
        <radialGradient id="blueFill" cx="0.62" cy="0.72" r="0.6">
          <stop offset="0" stop-color="#0a93d8"/>
          <stop offset="1" stop-color="#0455a3"/>
        </radialGradient>
      </defs>
      <path d="M128,343 C290,215 470,120 560,45 Q585,22 600,0 L600,73 C450,150 300,230 141,343 Z" fill="#555555"/>
      <path d="M141,343 C300,230 450,150 600,73 L600,343 Z" fill="url(#blueFill)"/>
      <path d="M141,343 C300,230 450,150 600,73" fill="none" stroke="#ffffff" stroke-width="2"/>
    </svg>

    <div class="brand">
      <div class="wordmark"><span>Larkspur Talent</span><span class="wordmark__dot"></span></div>
      <div class="tagline">Connecting Tech Talent</div>
    </div>

    <div class="person">
      <div class="person__name">Dana Whitfield</div>
      <div class="person__title">Manager</div>
    </div>

    <ul class="contact">
      <li class="contact__row">555-014-2290
        <svg class="contact__icon" viewBox="0 0 14 14" aria-hidden="true"><path d="M4 1 L6 4 L4.5 5.5 Q6 9 9 10 L10.5 8.5 L13 10.5 L11.5 13 Q5 12.5 1.5 4 Z" fill="#fff"/></svg>
      </li>
      <li class="contact__row">555-017-6841
        <svg class="contact__icon" viewBox="0 0 14 14" aria-hidden="true"><rect x="3.5" y="0.5" width="7" height="13" rx="1.2" fill="none" stroke="#fff"/><rect x="5" y="2.5" width="4" height="4" fill="#fff"/></svg>
      </li>
      <li class="contact__row">info@larkspurtalent.example
        <svg class="contact__icon" viewBox="0 0 14 14" aria-hidden="true"><rect x="1" y="3" width="12" height="8" fill="none" stroke="#fff"/><path d="M1 3 L7 8 L13 3" fill="none" stroke="#fff"/></svg>
      </li>
      <li class="contact__row">www.larkspurtalent.example
        <svg class="contact__icon" viewBox="0 0 14 14" aria-hidden="true"><g fill="none" stroke="#fff" stroke-width="0.9"><circle cx="7" cy="7" r="5.8"/><ellipse cx="7" cy="7" rx="2.6" ry="5.8"/><path d="M1.2 7 H12.8 M2.2 4 H11.8 M2.2 10 H11.8"/></g></svg>
      </li>
    </ul>
  </section>

  <section class="card card--back" aria-label="Business card back">
    <div class="brand">
      <div class="wordmark"><span>Larkspur Talent</span><span class="wordmark__dot"></span></div>
      <div class="tagline">Connecting Tech Talent</div>
    </div>
    <ul class="social">
      <li class="social__item"><span class="social__square"></span>Careerloop</li>
      <li class="social__item"><span class="social__square"></span>Blipster</li>
      <li class="social__item"><span class="social__square"></span>Myriada</li>
    </ul>
  </section>

</main>
</body>
</html>
```